Carpet cleaning company focused on high quality needs business cards

We are a growing company that just merged with another company and need to design a new business card. We do both residential as well as commercial cleaning. We do carpet, tile & grout, upholstery, hard floors, and stain & pet odor removal. We treat our customers like family and strive to achieve outstanding results with every job.

```html
<!DOCTYPE html>
<html lang="en">
<head>
<meta charset="utf-8">
<title>Brightway Floor Care – Business Cards</title>
<link href="https://fonts.googleapis.com/css2?family=Montserrat:wght@400;500;800&display=swap" rel="stylesheet">
<style>
  :root {
    --bg: #e9e9ec;
    --card: #ffffff;
    --red: #ea4540;
    --ink: #1c1c1c;
    --muted: #333333;
  }
  html, body {
    margin: 0;
    width: 1200px;
    height: 900px;
    overflow: hidden;
    background: var(--bg);
    font-family: "Montserrat", Arial, sans-serif;
  }
  .card {
    position: absolute;
    left: 250px;
    width: 700px;
    height: 400px;
    background: var(--card);
    border-radius: 26px;
    overflow: hidden;
    box-shadow: 0 10px 30px rgba(0,0,0,0.15);
  }
  .card--front { top: 30px; }
  .card--back  { top: 470px; }

  .card__stripe {
    position: absolute;
    left: 0; right: 0; bottom: 0;
    height: 34px;
    background: var(--red);
  }
  .card__rule {
    position: absolute;
    left: 0; right: 0; bottom: 40px;
    height: 4px;
    background: var(--ink);
  }

  .brand {
    position: absolute;
    display: flex;
    align-items: center;
    gap: 18px;
  }
  .brand__mark {
    background: var(--red);
    flex: none;
  }
  .brand__name {
    font-weight: 800;
    color: var(--ink);
    text-transform: uppercase;
    line-height: 0.95;
    letter-spacing: 0.5px;
  }
  .card--front .brand { left: 50%; top: 165px; transform: translateX(-50%); }
  .card--front .brand__mark { width: 90px; height: 90px; }
  .card--front .brand__name { font-size: 38px; }

  .card--back .brand { left: 60px; top: 210px; gap: 12px; }
  .card--back .brand__mark { width: 52px; height: 52px; }
  .card--back .brand__name { font-size: 22px; }

  .divider {
    position: absolute;
    left: 330px;
    top: 110px;
    width: 2px;
    height: 210px;
    background: var(--red);
  }
  .contact {
    position: absolute;
    left: 360px;
    top: 70px;
    color: var(--muted);
  }
  .contact__name {
    margin: 0;
    font-size: 30px;
    font-weight: 800;
    color: var(--red);
  }
  .contact__role {
    margin: 2px 0 16px;
    font-size: 15px;
    font-weight: 500;
  }
  .contact__address {
    margin: 0 0 8px;
    font-size: 15px;
    font-style: normal;
    line-height: 1.35;
  }
  .contact__list {
    list-style: none;
    margin: 0;
    padding: 0;
    font-size: 15px;
  }
  .contact__list li {
    display: flex;
    align-items: center;
    gap: 10px;
    height: 25px;
  }
  .contact__list svg { width: 14px; height: 14px; fill: var(--red); flex: none; }
</style>
</head>
<body>

<section class="card card--front" aria-label="Card front">
  <div class="brand">
    <span class="brand__mark"></span>
    <span class="brand__name">Brightway<br>Floor Care</span>
  </div>
  <div class="card__rule"></div>
  <div class="card__stripe"></div>
</section>

<section class="card card--back" aria-label="Card back">
  <div class="brand">
    <span class="brand__mark"></span>
    <span class="brand__name">Brightway<br>Floor Care</span>
  </div>
  <div class="divider"></div>
  <div class="contact">
    <h1 class="contact__name">Daniel Reyes</h1>
    <p class="contact__role">CEO</p>
    <address class="contact__address">418 Maple Grove Ave. #12<br>Riverton, OH 43190</address>
    <ul class="contact__list">
      <li>
        <svg viewBox="0 0 16 16"><path d="M3 1h3l1.5 4-2 1.3a9 9 0 0 0 4.2 4.2L11 8.5l4 1.5v3a2 2 0 0 1-2 2A12 12 0 0 1 1 3a2 2 0 0 1 2-2z"/></svg>
        555 013-4472
      </li>
      <li>
        <svg viewBox="0 0 16 16"><path d="M4 0h8a1 1 0 0 1 1 1v14a1 1 0 0 1-1 1H4a1 1 0 0 1-1-1V1a1 1 0 0 1 1-1zm1 2v10h6V2zm3 11a1 1 0 1 0 0 2 1 1 0 0 0 0-2z"/></svg>
        555 013-4473
      </li>
      <li>
        <svg viewBox="0 0 16 16"><path d="M0 3h16v1.5L8 9 0 4.5zm0 3.2 8 4.5 8-4.5V13H0z"/></svg>
        hello@brightwayfloor.com
      </li>
      <li>
        <svg viewBox="0 0 16 16"><circle cx="8" cy="8" r="7"/></svg>
        www.brightwayfloor.com
      </li>
    </ul>
  </div>
  <div class="card__rule"></div>
  <div class="card__stripe"></div>
</section>

</body>
</html>
```